Retail Jewelry Business Card Design Project

We are in need of a new business card design for a retail jewelry store. This store is in the business of fine jewelry including but not specific to bridal jewelry, diamonds, designer jewelry and watches.

This store has been in business for 20 years but continues to strive for a modern professional appeal. The main colors use for this business are a royal blue, white and silver.

Target Market(s)

Target market is ages 18-50

Industry/Entity Type

Jewelry

Requirements
Must have
• Sales Person Name
Sales Person Email Address

Store Address
Store Phone
Website

Standard business card size. No odd shapes or sizes.
Nice to have
• Overall modern feel for card.

We have thought that a design with a nice feature of the logo on the back of the card would be nice but open to ideas.
Should not have
• No specific images of jewelry should be used.

```html
<!DOCTYPE html>
<html lang="en">
<head>
<meta charset="utf-8">
<title>Marlowe Reed Fine Jewelry — Business Card</title>
<link rel="stylesheet" href="https://fonts.googleapis.com/css2?family=Tinos:ital,wght@0,400;0,700;1,700&family=Arimo:wght@400&display=swap">
<style>
  :root {
    --royal: #2e3192;
    --royal-soft: #6b6fc0;
    --white: #ffffff;
    --silver: #c9cbd1;
    --ink: #2b2b2b;
    --backdrop: #e6e6ec;
  }
  html, body {
    margin: 0;
    padding: 0;
    width: 1200px;
    height: 980px;
    overflow: hidden;
    background: var(--backdrop);
  }
  .sheet {
    position: relative;
    width: 1200px;
    height: 980px;
  }
  .card {
    position: absolute;
    width: 560px;
    height: 320px;
    border-radius: 28px;
    overflow: hidden;
    box-shadow: 0 6px 0 var(--silver), 0 14px 28px rgba(0,0,0,0.12);
  }

  /* Back of card */
  .card--back {
    left: 600px;
    top: 150px;
    background: var(--royal);
    color: var(--white);
    text-align: center;
  }
  .card--back .brand {
    margin: 92px 0 0;
    font-family: "Tinos", serif;
    font-weight: 400;
    font-size: 58px;
    line-height: 1;
    color: var(--white);
  }
  .card--back .brand-sub {
    margin: 14px 0 0;
    font-family: "Tinos", serif;
    font-weight: 700;
    font-size: 24px;
    letter-spacing: 5px;
    color: var(--white);
  }
  .card--back .web {
    margin: 40px 0 0;
    font-family: "Arimo", sans-serif;
    font-size: 16px;
    letter-spacing: 3px;
    color: var(--white);
  }

  /* Front of card */
  .card--front {
    left: 40px;
    top: 500px;
    background: var(--white);
  }
  .front-swoosh {
    position: absolute;
    inset: 0;
    width: 560px;
    height: 320px;
  }
  .front-brand {
    position: absolute;
    left: 150px;
    top: 26px;
    margin: 0;
    font-family: "Tinos", serif;
    font-weight: 400;
    font-size: 46px;
    line-height: 1;
    color: var(--royal);
  }
  .front-brand-sub {
    position: absolute;
    left: 186px;
    top: 82px;
    margin: 0;
    font-family: "Tinos", serif;
    font-weight: 700;
    font-size: 19px;
    letter-spacing: 4px;
    color: var(--royal);
  }
  .person {
    position: absolute;
    left: 56px;
    top: 118px;
    margin: 0;
    font-family: "Tinos", serif;
    font-style: italic;
    font-weight: 700;
    font-size: 19px;
    color: var(--royal);
  }
  .contact {
    position: absolute;
    left: 56px;
    top: 148px;
    margin: 0;
    padding: 0;
    list-style: none;
    font-family: "Tinos", serif;
    font-size: 16px;
    color: var(--ink);
  }
  .contact li {
    display: flex;
    align-items: center;
    gap: 8px;
    height: 22px;
  }
  .contact svg { width: 12px; height: 12px; flex: none; }
  .address {
    position: absolute;
    right: 34px;
    bottom: 18px;
    margin: 0;
    font-family: "Tinos", serif;
    font-style: normal;
    font-size: 17px;
    line-height: 1.3;
    color: var(--white);
    text-align: right;
  }
</style>
</head>
<body>
<main class="sheet">

  <section class="card card--back" aria-label="Card back">
    <p class="brand">Marlowe Reed</p>
    <p class="brand-sub">FINE JEWELRY</p>
    <p class="web">www.marlowereedjewelry.com</p>
  </section>

  <section class="card card--front" aria-label="Card front">
    <svg class="front-swoosh" viewBox="0 0 560 320" aria-hidden="true">
      <path d="M0 190 C 20 225, 80 236, 200 236 C 340 236, 470 222, 560 196 L560 320 L0 320 Z" fill="var(--royal)"/>
      <path d="M0 202 C 24 236, 90 246, 210 246 C 340 246, 460 236, 560 208" fill="none" stroke="var(--white)" stroke-width="2.5"/>
    </svg>

    <p class="front-brand">Marlowe Reed</p>
    <p class="front-brand-sub">FINE JEWELRY</p>

    <p class="person">Marlowe Reed Hartley</p>
    <ul class="contact">
      <li>
        <svg viewBox="0 0 12 12" aria-hidden="true"><circle cx="6" cy="6" r="5.5" fill="var(--royal-soft)"/><path d="M4 3.5 L5 3.5 L5.5 5 L4.8 5.6 C5.2 6.6 5.6 7 6.4 7.3 L7 6.6 L8.5 7.1 L8.5 8.2 C6 8.5 3.5 6 4 3.5 Z" fill="var(--white)"/></svg>
        555-218-4470
      </li>
      <li>
        <svg viewBox="0 0 12 12" aria-hidden="true"><rect x="0.5" y="2" width="11" height="8" rx="1.5" fill="var(--royal-soft)"/><path d="M1.5 3.2 L6 6.5 L10.5 3.2" fill="none" stroke="var(--white)" stroke-width="1"/></svg>
        marlowe@marlowereedjewelry.com
      </li>
      <li>
        <svg viewBox="0 0 12 12" aria-hidden="true"><circle cx="6" cy="6" r="5.5" fill="var(--royal-soft)"/><path d="M0.5 6 H11.5 M6 0.5 C3.5 3, 3.5 9, 6 11.5 M6 0.5 C8.5 3, 8.5 9, 6 11.5" fill="none" stroke="var(--white)" stroke-width="0.8"/></svg>
        www.marlowereedjewelry.com
      </li>
    </ul>

    <address class="address">482 Seabreeze Avenue<br>Port Linden, FL 32990</address>
  </section>

</main>
</body>
</html>
```